GTP biz card

We need a business card design for our new company based in Los Angeles called "Gold Tide Pictures". We develop film and television projects. We work with investors, financiers, film production companies, film distribution and sales companies as well as studios. We would like to incorporate our logo (see attached) on a two-sided card. We need to include: name and title, address, phone, email and company website.

Target Market(s)

Business, financial and studio clients

Industry/Entity Type

Business

Contact Information for Business Card

Two-sided. We are thinking of the logo on one side and the information on the back. Please feel free to be creative! Thanks.

Requirements
Must have
• Please include the following text information, excluding the "CAPS CATEGORY:" and please allow the ability for us to change the name, title and email address for each company employee):
• NAME & TITLE:
• Neil Parker
• Managing Partner
• COMPANY NAME:
• GOLD TIDE PICTURES (please use existing logo)
• COMPANY ADDRESS:
• KTW Studio Park
• 2250 Halverd Street
• Harbor Wing, 4th Floor
• Manhattan Beach, CA 90412
• COMPANY PHONE NUMBER:
• 310-555-0148
• COMPANY WEBSITE ADDRESS:
• www.goldtidepicturesgroup.example
• EMAIL ADDRESS: (only one per card)
• peter@goldtidepicturesgroup.example
• bingo@goldtidepicturesgroup.example
• neil@goldtidepicturesgroup.example

```html
<!DOCTYPE html>
<html lang="en">
<head>
<meta charset="utf-8">
<title>Gold Tide Pictures – Business Card</title>
<link href="https://fonts.googleapis.com/css2?family=Figtree:wght@400;500;600&display=swap" rel="stylesheet">
<style>
  :root {
    --backdrop: #e6e6e6;
    --card-white: #ffffff;
    --card-black: #000000;
    --ink: #1e1e1e;
    --accent: #2fb6e8;
  }
  * { margin: 0; padding: 0; box-sizing: border-box; }
  html, body {
    width: 1200px;
    height: 1000px;
    overflow: hidden;
  }
  body {
    position: relative;
    background: var(--backdrop);
    font-family: "Figtree", Arial, sans-serif;
    color: var(--ink);
  }
  .card {
    position: absolute;
    left: 308px;
    width: 543px;
    height: 318px;
  }
  .card--front { top: 122px; background: var(--card-white); }
  .card--back  { top: 522px; background: var(--card-black); }

  .brand-tile {
    position: absolute;
    left: 46px;
    top: 47px;
    width: 105px;
    height: 104px;
    background: var(--card-black);
    display: flex;
    flex-direction: column;
    align-items: center;
    justify-content: center;
    gap: 10px;
  }
  .brand-tile__dot {
    width: 30px;
    height: 30px;
    border-radius: 50%;
    background: var(--accent);
  }
  .brand-tile__name {
    font-size: 8px;
    font-weight: 600;
    letter-spacing: 0.5px;
    color: var(--accent);
    white-space: nowrap;
  }

  .contact {
    position: absolute;
    left: 173px;
    top: 44px;
  }
  .contact__name { font-size: 22px; font-weight: 500; line-height: 26px; }
  .contact__title { font-size: 17px; font-weight: 600; line-height: 22px; }
  .contact__email { font-size: 16px; font-weight: 400; line-height: 22px; }
  .contact__address {
    margin-top: 30px;
    font-size: 15px;
    line-height: 20px;
    font-style: normal;
  }
  .contact__web { margin-top: 21px; font-size: 17px; line-height: 22px; }

  .brand-mark {
    position: absolute;
    inset: 0;
    display: flex;
    flex-direction: column;
    align-items: center;
    justify-content: center;
    gap: 26px;
  }
  .brand-mark__dot {
    width: 70px;
    height: 70px;
    border-radius: 50%;
    background: var(--accent);
  }
  .brand-mark__name {
    font-size: 25px;
    font-weight: 600;
    letter-spacing: 2px;
    color: var(--accent);
    white-space: nowrap;
  }
</style>
</head>
<body>
  <section class="card card--front" aria-label="Card front">
    <div class="brand-tile">
      <span class="brand-tile__dot"></span>
      <span class="brand-tile__name">GOLD TIDE PICTURES</span>
    </div>
    <div class="contact">
      <p class="contact__name">Neil Parker</p>
      <p class="contact__title">Managing Partner</p>
      <p class="contact__email">neil@goldtidepicturesgroup.example</p>
      <address class="contact__address">
        KTW Studio Park<br>
        2250 Halverd Street<br>
        Harbor Wing, 4th Floor<br>
        Manhattan Beach, CA 90412<br>
        Phone: 310-555-0148
      </address>
      <p class="contact__web">www.goldtidepicturesgroup.example</p>
    </div>
  </section>

  <section class="card card--back" aria-label="Card back">
    <div class="brand-mark">
      <span class="brand-mark__dot"></span>
      <span class="brand-mark__name">GOLD TIDE PICTURES</span>
    </div>
  </section>
</body>
</html>
```